Corvel Capital LLC

Need Professional Business cards for New Investment Fund

Target Market(s)

High Quality investors

Industry/Entity Type

Financial

Contact Information for Business Card

Phone Number +1 555 284 6190
Name Lukas Varenko
Title Fund Manager
email lv@FundQuillmere.com
Website www.FundQuillmere.com

Colors

Designer to choose colors to be used in the design.

Requirements
Must have
• Must have our Logo and all of the above. Must be made so lettering and loge can be raised

```html
<!DOCTYPE html>
<html lang="en">
<head>
<meta charset="utf-8">
<title>Quillmere Capital LLC — Business Card</title>
<link rel="stylesheet" href="https://fonts.googleapis.com/css2?family=Questrial&display=swap">
<style>
  :root {
    --backdrop: #e4e4e4;
    --card-white: #f7f7f7;
    --card-panel: #ececec;
    --forest: #394a38;
    --forest-soft: #425341;
    --lime: #4fc43f;
    --lime-bright: #6fe05d;
    --ink-light: #e9efe8;
    --shadow: rgba(0, 0, 0, 0.14);
  }
  * { box-sizing: border-box; margin: 0; padding: 0; }
  html, body {
    width: 1200px;
    height: 900px;
    overflow: hidden;
    background: var(--backdrop);
    font-family: "Questrial", "Century Gothic", sans-serif;
  }
  .sheet {
    position: relative;
    width: 1200px;
    height: 900px;
    display: flex;
    flex-direction: column;
    align-items: center;
    justify-content: center;
    gap: 60px;
  }
  .card {
    position: relative;
    width: 630px;
    height: 360px;
    background: var(--card-white);
    overflow: hidden;
    box-shadow: 0 14px 30px var(--shadow);
  }
  .card-shape {
    position: absolute;
    inset: 0;
    width: 100%;
    height: 100%;
  }
  .brand {
    position: absolute;
    display: flex;
    align-items: center;
    gap: 10px;
    color: var(--forest);
    font-size: 28px;
    letter-spacing: 0.06em;
    white-space: nowrap;
  }
  .brand-mark {
    width: 14px;
    height: 14px;
    background: var(--lime);
  }
  .card-front .brand { left: 48px; top: 178px; }
  .card-back .brand { left: 50%; top: 118px; transform: translateX(-50%); }

  .identity {
    position: absolute;
    right: 44px;
    top: 44px;
    text-align: right;
  }
  .identity-name {
    color: var(--lime);
    font-size: 28px;
    letter-spacing: 0.03em;
    text-transform: uppercase;
    font-weight: 400;
  }
  .identity-name strong { font-weight: 400; color: var(--lime-bright); }
  .identity-title {
    color: var(--ink-light);
    font-size: 14px;
    margin-top: 4px;
  }
  .contacts {
    position: absolute;
    right: 44px;
    top: 176px;
    list-style: none;
    display: flex;
    flex-direction: column;
    gap: 14px;
  }
  .contact {
    display: flex;
    align-items: center;
    justify-content: flex-end;
    gap: 12px;
    color: var(--lime);
    font-size: 15px;
    letter-spacing: 0.02em;
    white-space: nowrap;
  }
  .contact-icon {
    width: 20px;
    height: 20px;
    flex: none;
  }
</style>
</head>
<body>
<main class="sheet">

  <section class="card card-front" aria-label="Business card front">
    <svg class="card-shape" viewBox="0 0 630 360" preserveAspectRatio="none" aria-hidden="true">
      <polygon points="150,0 630,0 630,360 400,360" fill="var(--forest)"/>
      <polygon points="400,360 630,360 630,300 375,320" fill="var(--forest-soft)" opacity="0.35"/>
    </svg>
    <div class="brand"><span class="brand-mark"></span>Quillmere</div>
    <div class="identity">
      <h1 class="identity-name">Lukas <strong>Varenko</strong></h1>
      <p class="identity-title">Fund Manager</p>
    </div>
    <ul class="contacts">
      <li class="contact">+1 555 284 6190
        <svg class="contact-icon" viewBox="0 0 20 20" aria-hidden="true">
          <rect width="20" height="20" rx="3" fill="var(--lime)"/>
          <path d="M6 5h3l1 3-2 1a7 7 0 0 0 3 3l1-2 3 1v3a1 1 0 0 1-1 1A10 10 0 0 1 5 6a1 1 0 0 1 1-1z" fill="var(--forest)"/>
        </svg>
      </li>
      <li class="contact">lv@FundQuillmere.com
        <svg class="contact-icon" viewBox="0 0 20 20" aria-hidden="true">
          <rect width="20" height="20" rx="3" fill="var(--lime)"/>
          <rect x="4" y="6" width="12" height="8" fill="none" stroke="var(--forest)" stroke-width="1.5"/>
          <path d="M4 6l6 5 6-5" fill="none" stroke="var(--forest)" stroke-width="1.5"/>
        </svg>
      </li>
      <li class="contact">www.FundQuillmere.com
        <svg class="contact-icon" viewBox="0 0 20 20" aria-hidden="true">
          <rect width="20" height="20" rx="3" fill="var(--lime)"/>
          <circle cx="10" cy="10" r="5.5" fill="none" stroke="var(--forest)" stroke-width="1.4"/>
          <path d="M4.5 10h11M10 4.5c-2.5 3-2.5 8 0 11M10 4.5c2.5 3 2.5 8 0 11" fill="none" stroke="var(--forest)" stroke-width="1.2"/>
        </svg>
      </li>
    </ul>
  </section>

  <section class="card card-back" aria-label="Business card back">
    <svg class="card-shape" viewBox="0 0 630 360" preserveAspectRatio="none" aria-hidden="true">
      <polygon points="0,210 260,250 630,360 0,360" fill="var(--forest)"/>
      <polygon points="260,250 630,250 630,360" fill="var(--card-panel)"/>
    </svg>
    <div class="brand"><span class="brand-mark"></span>Quillmere</div>
  </section>

</main>
</body>
</html>
```